Bespoke Builders Business Card Design

We need a business card for an established builder of high quality bespoke homes in Auckland and Northland. We build and renovate homes collaboratively facilitating effective communication between owners, builders, architects, suppliers and tradespeople. We have never built or renovated a home that leaks or has faults. We only use reliable materials. We have never been sued or had legal action taken against us. We are honest builders of bespoke homes not group mass produced homes. Our niche market is in character homes. We practice sustainability and have built a lot of coastal property. We have been in business for over thirty years . We would like to see natural colors of the environment sand,sea and maybe vegetation . The design should communicate quality, sustainability,fair pricing, open communication and the originality of bespoke building. And the fact that the builder is registered.

Industry/Entity Type

Business

Contact Information for Business Card

Rowan Tellick Builders
Ph. 021583917
18 Kestrel Rd Harwood Bay Auckland 0814
PO Box 927 Mangawhai 0583

```html
<!DOCTYPE html>
<html lang="en">
<head>
<meta charset="utf-8">
<title>Rowan Tellick Builders – Business Card</title>
<link rel="stylesheet" href="https://fonts.googleapis.com/css2?family=Libre+Bodoni:wght@500;700&family=Source+Sans+3:wght@400&display=swap">
<style>
  :root {
    --backdrop: #e7e4df;
    --card-black: #050505;
    --card-white: #f7f7f8;
    --navy: #2e2f86;
    --name-navy: #33379a;
    --text-light: #f1f1f1;
    --text-dark: #161616;
    --rule: #1c1c1c;
  }
  * { margin: 0; padding: 0; box-sizing: border-box; }
  html, body {
    width: 1200px;
    height: 902px;
    overflow: hidden;
    background: var(--backdrop);
  }
  .canvas {
    width: 1200px;
    height: 902px;
    display: flex;
    flex-direction: column;
    align-items: center;
    justify-content: center;
    gap: 42px;
  }
  .card {
    width: 700px;
    height: 400px;
    border: 7px solid var(--navy);
    position: relative;
    box-shadow: 0 6px 18px rgba(0,0,0,0.18);
  }
  .card-front {
    background: var(--card-black);
    display: flex;
    align-items: center;
    justify-content: center;
  }
  .card-front .company-name {
    font-family: "Libre Bodoni", "Bodoni Moda", serif;
    font-weight: 700;
    font-size: 50px;
    letter-spacing: 1px;
    color: var(--text-light);
    text-shadow: 0 0 6px rgba(255,255,255,0.35);
  }
  .card-back {
    background: var(--card-white);
  }
  .name-row {
    position: absolute;
    top: 118px;
    left: 0;
    right: 0;
    display: flex;
    align-items: center;
  }
  .name-row .rule {
    flex: 1;
    height: 2px;
    background: var(--rule);
  }
  .name-row .company-name {
    font-family: "Libre Bodoni", "Bodoni Moda", serif;
    font-weight: 700;
    font-size: 44px;
    color: var(--name-navy);
    padding: 0 10px;
    white-space: nowrap;
  }
  .contact {
    position: absolute;
    top: 200px;
    left: 0;
    right: 0;
    text-align: center;
    font-family: "Source Sans 3", "Myriad Pro", sans-serif;
    font-size: 25px;
    line-height: 34px;
    color: var(--text-dark);
  }
</style>
</head>
<body>
  <main class="canvas">
    <section class="card card-front" aria-label="Card front">
      <h1 class="company-name">Rowan Tellick Builders</h1>
    </section>
    <section class="card card-back" aria-label="Card back">
      <div class="name-row">
        <span class="rule"></span>
        <h2 class="company-name">Rowan Tellick Builders</h2>
        <span class="rule"></span>
      </div>
      <address class="contact" style="font-style:normal">
        <p class="phone">021583917</p>
        <p class="street">18 Kestrel Rd Harwood Bay Auckland 0814</p>
        <p class="po-box">PO Box 927 Mangawhai 0583</p>
      </address>
    </section>
  </main>
</body>
</html>
```